VELMOR Website Design

We need a website designed for our company VELMOR. We are a luxury lifestyle club that will provide benefits and services for our members. The site should be clean & sleek, preferably using black and white (or darker colors). (example sites: stravenhall.example, plinth.example)

Here is a link of a sample page I did using wix. (https://dunmere7.sitehostly.example/mysite) This can be used to get a general idea.

Target Market(s)

Upper Middle Class in the United States

Number of Pages Required

5+ page

Font styles to use
Sans Serif
Other font styles liked:
• Arial (or other similar fonts)

Requirements
Must have
• A clean design that is eye-catching and speaks to our company.
Nice to have
• Ideas for copy.

```html
<!DOCTYPE html>
<html lang="en">
<head>
<meta charset="utf-8">
<title>VELMOR — A Members Only Lifestyle Club</title>
<link href="https://fonts.googleapis.com/css2?family=Montserrat:wght@400;500;600;700&family=Open+Sans:ital,wght@0,400;0,600;1,400;1,600&display=swap" rel="stylesheet">
<style>
:root{
  --blue:#0a5ce6;
  --white:#ffffff;
  --text:#d9d9d9;
  --muted:#a8a8a8;
  --bg-hero:#3a3a3c;
  --bg-band:#2b2b2b;
  --bg-tabs:#1c1c1c;
  --bg-about:#232323;
  --bg-team:#2a2a2a;
  --bg-card:#1a1a1a;
  --bg-footer:#1e1e1e;
  --bg-bottom:#161616;
}
*{margin:0;padding:0;box-sizing:border-box}
html,body{width:1200px;height:3442px;overflow:hidden;background:var(--bg-team)}
body{position:relative;font-family:"Open Sans",Arial,sans-serif;color:var(--text)}
.abs{position:absolute}
.heading{font-family:"Montserrat",Arial,sans-serif;color:var(--white);font-weight:500;text-align:center}

/* hero */
.hero{left:0;top:0;width:1200px;height:654px;background:linear-gradient(160deg,#4a4644 0%,#2f2d2e 55%,#3b3836 100%)}
.logo{left:119px;top:16px;width:193px;height:53px;border:2px solid var(--white);font-family:"Montserrat",Arial,sans-serif;font-size:34px;font-weight:500;color:var(--white);display:flex;align-items:center;justify-content:center;letter-spacing:1px}
.nav{right:108px;top:34px;display:flex;gap:26px;align-items:center;font-family:"Montserrat",Arial,sans-serif;font-size:13px;color:var(--white)}
.nav .active{color:var(--blue);border-bottom:2px solid var(--blue);padding-bottom:4px}
.nav .search{width:22px;height:22px;border-radius:50%;background:var(--blue);display:flex;align-items:center;justify-content:center}
.hero-title{left:0;width:1200px;top:308px;font-size:46px;font-weight:600;letter-spacing:1px}
.hero-arrow{top:322px}
.dots{left:570px;top:577px;display:flex;gap:8px}
.dots span{width:11px;height:11px;border-radius:50%;background:var(--white)}
.dots span.on{background:var(--blue)}

/* about */
.about-band{left:0;top:654px;width:1200px;height:103px;background:var(--bg-band)}
.section-title{font-size:40px;font-weight:500;letter-spacing:1px}
.tabs{left:0;top:757px;width:1200px;height:51px;background:var(--bg-tabs);font-size:12px;color:var(--white)}
.tab{top:0;height:51px;display:flex;align-items:center;justify-content:center;border-left:1px solid #3a3a3a}
.about{left:0;top:808px;width:1200px;height:459px;background:var(--bg-about)}
.photo{display:block}
.club-title{left:110px;top:1042px;font-family:"Montserrat",Arial,sans-serif;font-size:28px;color:var(--white);font-weight:500}
.club-text{left:110px;top:1088px;width:475px;font-size:11.5px;line-height:20px;color:var(--text)}
.feature{left:610px;width:480px;height:64px}
.feature .icon{position:absolute;left:0;top:0;width:60px;height:60px;border-radius:50%;background:var(--blue);display:flex;align-items:center;justify-content:center}
.feature h4{position:absolute;left:85px;top:0;font-family:"Montserrat",Arial,sans-serif;font-size:11px;font-weight:600;color:var(--blue);letter-spacing:.5px}
.feature p{position:absolute;left:85px;top:20px;width:390px;font-size:11px;line-height:22px;color:var(--text)}

/* team */
.team{left:0;top:1267px;width:1200px;height:936px;background:var(--bg-team)}
.team-sub{left:0;width:1200px;top:1354px;font-style:italic;font-weight:600;font-size:19px;color:var(--white);text-align:center}
.card{width:308px;height:346px;background:var(--bg-card)}
.card .portrait{position:absolute;left:0;top:0;width:308px;height:207px}
.card .badge{position:absolute;left:128px;top:180px;width:52px;height:52px;border-radius:50%;background:var(--blue);display:flex;align-items:center;justify-content:center}
.card .name{position:absolute;left:0;width:308px;top:242px;text-align:center;font-family:"Montserrat",Arial,sans-serif;font-size:14px;color:var(--white);letter-spacing:.5px}
.card .rule{position:absolute;left:124px;top:264px;width:60px;height:1px;background:#666}
.card .bio{position:absolute;left:28px;width:252px;top:276px;text-align:center;font-size:11px;line-height:22px;color:var(--text)}
.card.featured{background:var(--blue)}
.card.featured .portrait{height:152px}
.card.featured .badge{top:125px;background:var(--blue)}
.card.featured .name{top:188px}
.card.featured .rule{top:210px;background:#9ec0ff}
.card.featured .bio{top:222px;color:var(--white)}
.socials{position:absolute;left:96px;top:302px;display:flex;gap:8px}
.socials span{width:30px;height:30px;border-radius:50%;border:1.5px solid var(--white)}

/* call to action */
.cta{left:0;top:2203px;width:1200px;height:459px;background:linear-gradient(180deg,#26313a 0%,#1f2a31 45%,#23343d 70%,#2c2f31 100%)}
.cta-brand{left:0;width:1200px;top:2326px;font-size:30px;font-weight:600;letter-spacing:2px}
.cta-line{left:0;width:1200px;top:2366px;font-size:30px;font-weight:600;line-height:42px;letter-spacing:1.5px}
.btn{left:544px;top:2470px;width:112px;height:39px;border:2px solid var(--white);display:flex;align-items:center;justify-content:center;font-family:"Montserrat",Arial,sans-serif;font-size:13px;color:var(--white);letter-spacing:1px}

/* testimonials */
.testi-band{left:0;top:2662px;width:1200px;height:152px;background:var(--bg-band)}
.testi-sub{left:0;width:1200px;top:2742px;text-align:center;font-style:italic;font-size:20px;color:var(--white)}
.testi{left:0;top:2814px;width:1200px;height:387px;background:var(--bg-card)}
.quote{left:404px;top:2846px;width:720px;font-size:19px;line-height:40px;color:var(--white)}
.author{top:3103px;width:379px;height:98px;text-align:center;padding-top:18px}
.author small{display:block;font-family:"Montserrat",Arial,sans-serif;font-size:10px;letter-spacing:.5px;color:#c9c9c9}
.author b{display:block;margin-top:4px;font-family:"Montserrat",Arial,sans-serif;font-size:24px;font-weight:500;color:var(--white);letter-spacing:1px}
.author.on{background:var(--blue)}

/* footer */
.footer{left:0;top:3201px;width:1200px;height:200px;background:var(--bg-footer);font-size:11px;line-height:18px;color:var(--text)}
.footer h5{font-size:11px;font-weight:400;color:var(--blue)}
.f-socials{display:flex;gap:12px}
.f-socials span{width:26px;height:26px;border-radius:50%;border:1.5px solid #999}
.email{width:150px;height:28px;border:1px solid #555;border-radius:14px;font-size:10px;color:#888;padding:6px 12px;position:relative}
.bottom{left:0;top:3401px;width:1200px;height:41px;background:var(--bg-bottom);display:flex;align-items:center;justify-content:center}
</style>
</head>
<body>

<!-- Hero -->
<section class="abs hero" role="img" aria-label="Photo of club members raising wine glasses at a dinner table"></section>
<div class="abs logo">VELMOR</div>
<nav class="abs nav">
  <span class="active">Home</span><span>About us</span><span>Services &amp; Benefits</span><span>Contact</span>
  <span class="search"><svg width="11" height="11" viewBox="0 0 11 11"><circle cx="4.5" cy="4.5" r="3.3" fill="none" stroke="#fff" stroke-width="1.5"/><line x1="7" y1="7" x2="10" y2="10" stroke="#fff" stroke-width="1.5"/></svg></span>
</nav>
<h1 class="abs heading hero-title">A MEMBERS ONLY LIFESTYLE CLUB</h1>
<svg class="abs hero-arrow" style="left:38px" width="22" height="34" viewBox="0 0 22 34"><polyline points="18,3 4,17 18,31" fill="none" stroke="#fff" stroke-width="4"/></svg>
<svg class="abs hero-arrow" style="left:1130px" width="22" height="34" viewBox="0 0 22 34"><polyline points="4,3 18,17 4,31" fill="none" stroke="#fff" stroke-width="4"/></svg>
<div class="abs dots"><span class="on"></span><span></span><span></span></div>
<svg class="abs" style="left:562px;top:620px" width="76" height="34" viewBox="0 0 76 34"><polygon points="38,0 76,34 0,34" fill="#0a5ce6"/><polyline points="31,20 38,26 45,20" fill="none" stroke="#fff" stroke-width="2.5"/></svg>

<!-- About -->
<section class="abs about-band"></section>
<h2 class="abs heading section-title" style="left:0;width:1200px;top:678px">ABOUT US</h2>
<div class="abs tabs">
  <div class="abs tab" style="left:110px;width:138px">Services</div>
  <div class="abs tab" style="left:248px;width:108px">Experiences</div>
  <div class="abs tab" style="left:356px;width:121px;border-right:1px solid #3a3a3a">About VELMOR</div>
</div>
<section class="abs about"></section>
<div class="abs photo" style="left:110px;top:863px;width:475px;height:161px;background:linear-gradient(180deg,#2a52a8 0%,#6a86b8 45%,#c89a5a 70%,#3f5a2a 100%)" role="img" aria-label="Photo of a luxury villa lit up at dusk with gardens and pool"></div>
<h3 class="abs club-title">LIFESTYLE CLUB</h3>
<p class="abs club-text">Lorem ipsum dolor sit amet, consectetur adipiscing elit. Aenean egestas eu leo nec eleifend. Nulla sapien turpis, convallis ac ultrices sed, aliquam sit amet arcu. Phasellus est orci, bibendum consequat quam sit amet, facilisis pharetra nisl. Nullam ultrices mi quam, et volutpat magna suscipit eget.</p>

<div class="abs feature" style="top:856px">
  <span class="icon"><svg width="22" height="14" viewBox="0 0 22 14"><polyline points="3,12 11,4 19,12" fill="none" stroke="#fff" stroke-width="3.5"/></svg></span>
  <h4>BENEFITS AND SERVICES</h4>
  <p>VELMOR membership provides you with amazing benefits and services.</p>
</div>
<div class="abs feature" style="top:993px">
  <span class="icon"><svg width="22" height="14" viewBox="0 0 22 14"><polyline points="3,12 11,4 19,12" fill="none" stroke="#fff" stroke-width="3.5"/></svg></span>
  <h4>EXPERIENCES</h4>
  <p>VELMOR organizes and supports a ton of private events and parties for our members.</p>
</div>
<div class="abs feature" style="top:1122px">
  <span class="icon"><svg width="22" height="14" viewBox="0 0 22 14"><polyline points="3,12 11,4 19,12" fill="none" stroke="#fff" stroke-width="3.5"/></svg></span>
  <h4>ABOUT VELMOR</h4>
  <p>VELMOR is a members only lifestyle club founded in order to bring the best services, experiences, and opportunities to our diverse community of members.</p>
</div>

<!-- Team -->
<section class="abs team"></section>
<h2 class="abs heading section-title" style="left:0;width:1200px;top:1298px">OUR TEAM</h2>
<p class="abs team-sub">Morbi leo risus, porta ac consectetur ac, vestibulum at eros.</p>

<div class="abs card" style="left:112px;top:1423px">
  <div class="portrait" style="background:linear-gradient(180deg,#3c3c3c,#242424)" role="img" aria-label="Portrait photo of team member Dorian Pell"></div>
  <span class="badge"><svg width="20" height="13" viewBox="0 0 22 14"><polyline points="3,12 11,4 19,12" fill="none" stroke="#fff" stroke-width="3.5"/></svg></span>
  <div class="name">DORIAN PELL</div><div class="rule"></div>
  <p class="bio">Morbi leo risus, porta ac consectetur ac, vestibulum at eros. Lorem ipsum dolor sit amet, consectetur adipiscing elit.</p>
</div>
<div class="abs card featured" style="left:447px;top:1423px">
  <div class="portrait" style="background:linear-gradient(180deg,#4a4a4a,#2e2e2e)" role="img" aria-label="Portrait photo of team member Marcus Holt"></div>
  <span class="badge"><svg width="20" height="13" viewBox="0 0 22 14"><polyline points="3,12 11,4 19,12" fill="none" stroke="#fff" stroke-width="3.5"/></svg></span>
  <div class="name">MARCUS HOLT</div><div class="rule"></div>
  <p class="bio">Morbi leo risus, porta ac consectetur ac, vestibulum at eros. Lorem ipsum dolor sit amet, consectetur adipiscing elit.</p>
  <div class="socials"><span></span><span></span><span></span></div>
</div>
<div class="abs card" style="left:780px;top:1423px">
  <div class="portrait" style="background:linear-gradient(180deg,#3a3a3a,#262626)" role="img" aria-label="Portrait photo of team member Renata Vale"></div>
  <span class="badge"><svg width="20" height="13" viewBox="0 0 22 14"><polyline points="3,12 11,4 19,12" fill="none" stroke="#fff" stroke-width="3.5"/></svg></span>
  <div class="name">RENATA VALE</div><div class="rule"></div>
  <p class="bio">Morbi leo risus, porta ac consectetur ac, vestibulum at eros. Lorem ipsum dolor sit amet, consectetur adipiscing elit.</p>
</div>

<div class="abs card" style="left:112px;top:1797px">
  <div class="portrait" style="background:linear-gradient(180deg,#4a4542,#2c2a29)" role="img" aria-label="Portrait photo of team member Dorian Pell"></div>
  <span class="badge"><svg width="20" height="13" viewBox="0 0 22 14"><polyline points="3,12 11,4 19,12" fill="none" stroke="#fff" stroke-width="3.5"/></svg></span>
  <div class="name">DORIAN PELL</div><div class="rule"></div>
  <p class="bio">Morbi leo risus, porta ac consectetur ac, vestibulum at eros. Lorem ipsum dolor sit amet, consectetur adipiscing elit.</p>
</div>
<div class="abs card" style="left:447px;top:1797px">
  <div class="portrait" style="background:linear-gradient(180deg,#3e3e3e,#262626)" role="img" aria-label="Portrait photo of team member Irena Solvik"></div>
  <span class="badge"><svg width="20" height="13" viewBox="0 0 22 14"><polyline points="3,12 11,4 19,12" fill="none" stroke="#fff" stroke-width="3.5"/></svg></span>
  <div class="name">IRENA SOLVIK</div><div class="rule"></div>
  <p class="bio">Morbi leo risus, porta ac consectetur ac, vestibulum at eros. Lorem ipsum dolor sit amet, consectetur adipiscing elit.</p>
</div>
<div class="abs card" style="left:780px;top:1797px">
  <div class="portrait" style="background:linear-gradient(180deg,#4d4a47,#2b2928)" role="img" aria-label="Portrait photo of team member Helena Ward"></div>
  <span class="badge"><svg width="20" height="13" viewBox="0 0 22 14"><polyline points="3,12 11,4 19,12" fill="none" stroke="#fff" stroke-width="3.5"/></svg></span>
  <div class="name">HELENA WARD</div><div class="rule"></div>
  <p class="bio">Morbi leo risus, porta ac consectetur ac, vestibulum at eros. Lorem ipsum dolor sit amet, consectetur adipiscing elit.</p>
</div>

<!-- Call to action -->
<section class="abs cta" role="img" aria-label="Photo of a resort terrace with a swimming pool overlooking the sea at dusk"></section>
<div class="abs heading cta-brand">VELMOR</div>
<p class="abs heading cta-line">MEMBERSHIP PROVIDES YOU WITH AMAZING BENEFITS AND<br>SERVICES.</p>
<div class="abs btn">VISIT</div>

<!-- Testimonials -->
<section class="abs testi-band"></section>
<h2 class="abs heading" style="left:0;width:1200px;top:2692px;font-size:30px">TESTIMONIALS</h2>
<p class="abs testi-sub">Dummy text of the printing and typesetting</p>
<section class="abs testi"></section>
<div class="abs" style="left:0;top:2814px;width:379px;height:289px;background:linear-gradient(180deg,#9fb4c4 0%,#6d7f8c 40%,#b38a5a 70%,#4a3a2c 100%)" role="img" aria-label="Photo of a yacht deck at sunset on open water"></div>
<p class="abs quote">Lorem Ipsum is simply dummy text of the printing and typesetting industry. Lorem Ipsum has been the industry's standard dummy text ever since the 1500s, when an unknown printer took a galley of type and scrambled it to make a type specimen book. It has survived not only five centuries, but also the leap into electronic typesetting, remaining.</p>
<div class="abs author on" style="left:0"><small>OWEN TARRANT</small><b>CO-FOUNDER</b></div>
<div class="abs author" style="left:357px"><small>CLARA BENNING</small><b>FOUNDER</b></div>
<div class="abs author" style="left:695px"><small>VICTOR ASHBY</small><b>MANAGER</b></div>

<!-- Footer -->
<footer class="abs footer">
  <div class="abs" style="left:112px;top:68px">
    <p>Copyright 2017-18 <span style="color:var(--blue)">VELMOR</span></p>
    <div class="f-socials" style="margin-top:24px"><span></span><span></span><span></span><span></span></div>
  </div>
  <div class="abs" style="left:445px;top:68px">
    <h5>Our location</h5>
    <p style="margin-top:14px;line-height:16px">Northbay Holdings LLC 4821 Linden Ave,<br>Suite 210 Fairhaven, IL 00000<br>Phone : +00 1 55501234<br>Email : info@velmor.example</p>
  </div>
  <div class="abs" style="left:778px;top:68px;width:320px">
    <h5>Keep in touch</h5>
    <p style="margin-top:8px">Lorem ipsum dolor sit amet, consectetur adi sollicitud ante tellus ornare mi, et mollis</p>
    <div class="email" style="margin-top:10px">Your email
      <svg style="position:absolute;right:10px;top:9px" width="10" height="8" viewBox="0 0 10 8"><polyline points="0,4 9,4" stroke="#aaa" stroke-width="1.3"/><polyline points="6,1 9,4 6,7" fill="none" stroke="#aaa" stroke-width="1.3"/></svg>
    </div>
  </div>
</footer>
<div class="abs bottom"><svg width="18" height="11" viewBox="0 0 18 11"><polyline points="2,9 9,2 16,9" fill="none" stroke="#fff" stroke-width="2.5"/></svg></div>

</body>
</html>
```